Amber Hollow Gin bottle label

We are looking for a label design for our new gin 'Amber Hollow Gin' The gin will be transparent and be in a 50cl bottle at 40%abv. The type of bottle we are using is on the attachment. We would like the label to be shabby chic style in design, suitable as a wedding gift, for couples, valentines, anniversarys.
'CAN YOU PLEASE SEE THE ATTACHMENT AS TO STYLE OF DESIGN'
Thank you

```html
<!DOCTYPE html>
<html lang="en">
<head>
<meta charset="utf-8">
<title>Amber Hollow Gin – Bottle Label</title>
<link href="https://fonts.googleapis.com/css2?family=Great+Vibes&family=Cormorant+Garamond:wght@500&display=swap" rel="stylesheet">
<style>
  :root {
    --page: #eef0f3;
    --label-ground: #cfd4dc;
    --frame-brown: #5b3322;
    --heart-pink: #d98aa8;
    --heart-pink-deep: #c97397;
    --script-brown: #5a2a1e;
    --gin-red: #8b3526;
    --rose-peach: #eab29c;
    --rose-leaf: #9fbfae;
    --small-text: #4a4a4a;
  }
  html, body {
    margin: 0;
    width: 795px;
    height: 1200px;
    overflow: hidden;
    background: var(--page);
  }
  .label {
    position: relative;
    width: 795px;
    height: 1200px;
    background: var(--label-ground);
  }
  .label-frame {
    position: absolute;
    inset: 0;
  }
  .title-heart {
    position: absolute;
    left: 100px;
    top: 70px;
    width: 595px;
    height: 520px;
  }
  .brand-name {
    position: absolute;
    left: 0;
    right: 0;
    top: 215px;
    margin: 0;
    text-align: center;
    font-family: "Great Vibes", cursive;
    font-weight: 400;
    font-size: 96px;
    line-height: 1;
    color: var(--script-brown);
  }
  .spirit-name {
    position: absolute;
    left: 0;
    right: 0;
    top: 455px;
    margin: 0;
    text-align: center;
    font-family: "Cormorant Garamond", serif;
    font-weight: 500;
    font-size: 92px;
    letter-spacing: 2px;
    line-height: 1;
    color: var(--gin-red);
  }
  .rose-spray {
    position: absolute;
    left: 110px;
    top: 610px;
    width: 580px;
    height: 470px;
    border-radius: 46% 54% 40% 50% / 45% 40% 55% 50%;
    background: radial-gradient(ellipse at 50% 55%, var(--rose-peach) 0%, #e3b7a6 45%, var(--rose-leaf) 78%, rgba(159,191,174,0) 100%);
  }
  .abv {
    position: absolute;
    right: 150px;
    top: 1070px;
    margin: 0;
    font-family: "Cormorant Garamond", serif;
    font-size: 26px;
    color: var(--small-text);
  }
</style>
</head>
<body>
  <main class="label">
    <svg class="label-frame" viewBox="0 0 795 1200" aria-hidden="true">
      <path d="M28 30 L300 27 L520 32 L767 28 L764 300 L769 620 L765 900 L768 1172 L500 1168 L260 1173 L27 1170 L31 880 L26 560 L30 260 Z"
            fill="none" stroke="var(--frame-brown)" stroke-width="6" stroke-linejoin="round"/>
    </svg>

    <svg class="title-heart" viewBox="0 0 595 520" aria-hidden="true">
      <path d="M297 505 C180 420 20 320 20 165 C20 70 95 12 175 12 C235 12 275 45 297 85 C319 45 359 12 420 12 C500 12 575 70 575 165 C575 320 415 420 297 505 Z"
            fill="var(--heart-pink)" opacity="0.9"/>
      <path d="M297 372 C276 356 262 344 262 328 C262 317 270 310 280 310 C288 310 294 315 297 321 C300 315 306 310 314 310 C324 310 332 317 332 328 C332 344 318 356 297 372 Z"
            fill="var(--heart-pink-deep)"/>
    </svg>

    <h1 class="brand-name">Amber Hollow</h1>
    <h2 class="spirit-name">GIN</h2>

    <div class="rose-spray" role="img" aria-label="Illustration of a spray of peach roses with eucalyptus leaves"></div>

    <p class="abv">40%abv</p>
  </main>
</body>
</html>
```